Website Design for WestaKolory.pl – Luxury Wedding Car Rental with Chauffeur

We are looking for a talented designer to create a modern, elegant, and fully responsive website for our new brand – WestyKolory.pl. We are a premium car rental platform in Poland, offering luxury and exotic vehicles exclusively for weddings. All cars come with a professional chauffeur, ensuring a high-end, stress-free, and stylish experience.
Website Purpose:
The website should present our offering in a luxurious, clear, and inspiring way. It must build trust, highlight the prestige of our brand, and encourage inquiries. Our target audience includes engaged couples, wedding planners, and clients seeking a truly exceptional vehicle for their special day.
Design Requirements:
Style: modern, elegant, minimalist
Color palette: white, black, gold, optionally silver – refined and luxurious
Typography: clean, modern, high-end
Layout: clear, intuitive, with large car images and well-defined sections
Fully responsive (desktop, tablet, mobile)
Bilingual layout (Polish/English) must be considered
Pages to Design:
Homepage
About Us
Fleet Overview
Individual Car Pages
Services (Weddings, Photo Shoots, Film Rentals)
Why Us / Unique Selling Points
Contact
FAQ
Inspiration:
Luxury automotive brands (e.g. Varnel-Hoske, Corvash, Elbrin Tusko)
High-end wedding websites
Minimalist layouts with large visuals and elegant typography
Additional Notes:
The design should evoke the emotions of a wedding day – elegance, uniqueness, style, and class. Please avoid flashy colors, excessive graphic effects, or overly decorative elements. Subtlety, prestige, and sophistication are key.

```html
<!DOCTYPE html>
<html lang="en">
<head>
<meta charset="utf-8">
<title>WestaKolory.pl – Luxury Wedding Cars</title>
<link rel="stylesheet" href="https://fonts.googleapis.com/css2?family=Cinzel:wght@400;600;700&family=Montserrat:wght@400;500;600;700&family=Anton&display=swap">
<style>
:root{
  --gold:#d9bf5f;
  --gold-dark:#b89a3a;
  --black:#0b0b0b;
  --ink:#1b1b1b;
  --grey:#6f6f6f;
  --light:#f1f1f1;
  --line:#dddddd;
  --white:#ffffff;
}
*{box-sizing:border-box;margin:0;padding:0}
html,body{width:1200px;height:5169px;overflow:hidden;background:var(--white)}
body{font-family:'Montserrat',sans-serif;color:var(--ink);position:relative}
.sec{position:absolute;left:0;width:1200px}
.abs{position:absolute}
.serif{font-family:'Cinzel',serif}
.ph{position:absolute;border-radius:10px}
.btn{position:absolute;display:flex;align-items:center;justify-content:center;border-radius:30px;font-size:12px;font-weight:600;letter-spacing:1px;text-transform:uppercase}
.btn-gold{background:var(--gold);color:var(--black)}
.btn-line{border:1px solid var(--gold);color:var(--gold-dark)}
p.small{font-size:12px;line-height:1.7;color:var(--grey)}

/* hero */
.hero{top:0;height:640px;background:linear-gradient(100deg,#1e2618 0%,#3a4330 40%,#8b8a78 70%,#4b4a3c 100%)}
.nav{position:absolute;top:20px;left:30px;right:30px;height:60px;display:flex;align-items:center}
.brand{font-family:'Montserrat',sans-serif;font-weight:600;font-size:20px;color:var(--gold)}
.nav-links{display:flex;gap:34px;margin-left:150px;font-size:12px;color:var(--white)}
.nav-cta{margin-left:auto;border:1px solid var(--gold);color:var(--gold);border-radius:20px;padding:8px 20px;font-size:11px;font-weight:600}
.nav-dot{width:26px;height:26px;border:1px solid var(--white);border-radius:50%;margin-left:12px}
.hero h1{position:absolute;left:112px;top:168px;font-family:'Cinzel',serif;font-weight:600;font-size:46px;line-height:1.15;color:var(--white);letter-spacing:1px}
.hero .lead{position:absolute;left:112px;top:290px;font-size:15px;color:#e6e6e6}

/* intro */
.intro{top:740px;height:260px}
.card-hire{position:absolute;left:440px;top:20px;width:315px;height:215px;background:var(--light);border-radius:6px;padding:22px 28px;text-align:center;display:flex;flex-direction:column;align-items:center}
.card-hire h3{font-family:'Cinzel',serif;font-size:14px;letter-spacing:1px;margin-bottom:10px}
.card-hire p.small{line-height:1.6}
.card-hire .more{margin-top:auto;display:flex;align-items:center;justify-content:center;width:80px;height:26px;border:1px solid var(--gold);color:var(--gold-dark);border-radius:30px;font-size:9px;font-weight:600;letter-spacing:1px;text-transform:uppercase}

/* why */
.why{top:1065px;height:260px}
.why h2{position:absolute;left:112px;top:110px;font-family:'Cinzel',serif;font-size:30px;font-weight:600}
.feature{position:absolute;top:5px;width:255px;height:240px;border-radius:10px;background:var(--white);box-shadow:0 4px 18px rgba(0,0,0,.08);padding:28px 24px}
.feature h4{font-family:'Cinzel',serif;font-size:14px;font-weight:700;margin:22px 0 10px}
.feature.gold{background:var(--gold)}
.feature.gold p.small{color:#3a3214}
.icon-box{width:64px;height:64px;border-radius:10px;background:var(--white);display:flex;align-items:center;justify-content:center}
.icon-circle{width:64px;height:64px;border-radius:50%;background:var(--gold);display:flex;align-items:center;justify-content:center}

/* featured */
.featured{top:1397px;height:570px;left:24px;width:1152px;background:var(--black);border-radius:26px;overflow:hidden}
.featured h2{position:absolute;left:88px;top:60px;font-family:'Cinzel',serif;font-size:30px;color:var(--white);font-weight:600}
.tab{position:absolute;top:62px;height:34px;padding:0 22px;border-radius:20px;font-size:10px;font-weight:600;letter-spacing:1px;display:flex;align-items:center}
.tab.on{background:var(--gold);color:var(--black)}
.tab.off{border:1px solid var(--gold);color:var(--white)}
.car-name{position:absolute;top:412px;font-family:'Cinzel',serif;color:var(--white);font-size:14px;font-weight:600}
.car-price{position:absolute;top:436px;font-size:11px;color:#bbb}
.car-link{position:absolute;top:458px;font-size:10px;color:var(--gold);font-weight:600;text-decoration:underline}

/* about */
.about{top:2047px;height:630px}
.about h2{position:absolute;left:600px;top:18px;font-family:'Cinzel',serif;font-size:30px;font-weight:600}
.about .txt{position:absolute;left:600px;top:80px;width:485px}
.about .txt p{margin-bottom:14px}
.offer{position:absolute;left:140px;top:470px;color:var(--white)}

/* faq */
.faq{top:2741px;height:540px}
.faq h2{position:absolute;left:112px;top:0;font-family:'Cinzel',serif;font-size:30px;font-weight:600}
.faq-row{position:absolute;left:112px;width:973px;border-bottom:1px solid var(--line);font-size:13px;font-weight:500}
.plus{position:absolute;right:8px;top:0;font-size:20px;font-weight:500}

/* testimonials */
.testi{top:3363px;height:420px;left:24px;width:1152px;background:var(--gold);border-radius:26px;overflow:hidden}
.testi h2{position:absolute;left:0;right:0;top:40px;text-align:center;font-family:'Cinzel',serif;font-size:28px;font-weight:600}
.review{position:absolute;top:120px;width:470px;height:240px;background:var(--white);border-radius:6px;padding:28px 30px}
.quote{position:absolute;right:30px;top:16px;font-family:'Cinzel',serif;font-size:70px;color:#cfcfcf;line-height:1}
.avatar{width:50px;height:50px;border-radius:4px;background:linear-gradient(#8b7b6a,#3d3631)}
.who{position:absolute;left:98px;top:32px}
.who b{font-size:14px;display:block}
.who span{font-size:11px;color:var(--grey)}

/* blogs */
.blogs{top:3873px;height:450px}
.blogs h2{position:absolute;left:112px;top:0;font-family:'Anton',sans-serif;font-size:36px;letter-spacing:1px}
.post-title{font-size:15px;font-weight:700;margin-bottom:6px}
.meta{font-size:11px;color:var(--grey)}
.read{font-size:11px;color:var(--gold-dark);font-weight:600;margin-top:8px}

/* cta */
.cta{top:4402px;height:353px;background:linear-gradient(90deg,#0d0d0f 0%,#1c2130 45%,#2f3d56 75%,#151922 100%)}
.cta h2{position:absolute;left:112px;top:90px;font-family:'Cinzel',serif;font-size:44px;line-height:1.15;color:var(--white);font-weight:400}

/* footer */
.footer{top:4755px;height:414px;background:var(--black);color:#cfcfcf}
.fcol{position:absolute;top:40px;font-size:12px;line-height:2.1}
.fcol h5{font-size:13px;color:var(--white);font-weight:600;letter-spacing:1px;margin-bottom:8px}
.social{position:absolute;top:210px;left:112px;display:flex;gap:10px}
.social span{width:30px;height:30px;border-radius:50%;background:var(--gold)}
.copy{position:absolute;left:0;right:0;top:378px;text-align:center;font-size:11px;color:#aaa}
</style>
</head>
<body>

<section class="sec hero">
  <div class="ph" style="left:0;top:0;width:1200px;height:640px;border-radius:0;background:linear-gradient(100deg,#1e2618 0%,#3a4330 38%,#a9a698 62%,#56543f 100%)" role="img" aria-label="Bride and groom standing beside a vintage white wedding car in a green park"></div>
  <nav class="nav">
    <span class="brand">WestaKolory.pl</span>
    <div class="nav-links"><span>About</span><span>Services</span><span>Fleet Overview</span><span>Why Choose Us</span><span>FAQ</span><span>Testimonials</span></div>
    <span class="nav-cta">CONTACT US</span>
    <span class="nav-dot"></span><span class="nav-dot"></span>
  </nav>
  <h1>LUXURY CARS FOR YOUR<br>SPECIAL DAY</h1>
  <p class="lead">With a professional chauffeur, stress-free and stylish.</p>
  <div class="btn btn-gold" style="left:112px;top:330px;width:190px;height:42px">View our fleet</div>
</section>

<section class="sec intro">
  <div class="ph" style="left:112px;top:0;width:318px;height:250px;background:linear-gradient(135deg,#cfc9c0,#6b5d52)" role="img" aria-label="Bride in a white dress beside a small white classic car"></div>
  <div class="card-hire">
    <h3>WEDDING CAR HIRE</h3>
    <p class="small">Arrive in style with our elegant wedding cars, each driven by a professional chauffeur. We take care of timing, route and comfort so you can enjoy every moment together.</p>
    <span class="more">Read all</span>
  </div>
  <div class="ph" style="left:795px;top:0;width:320px;height:250px;background:linear-gradient(135deg,#e3d7c5,#7a3f2a)" role="img" aria-label="Wedding couple seen through the open door of a classic car"></div>
</section>

<section class="sec why">
  <h2>WHY CHOOSE US</h2>
  <svg class="abs" style="left:112px;top:168px" width="80" height="20" viewBox="0 0 80 20"><path d="M2 10h28M2 10l6-6M2 10l6 6" stroke="#1b1b1b" stroke-width="2" fill="none"/><path d="M50 10h28M78 10l-6-6M78 10l-6 6" stroke="#b89a3a" stroke-width="2" fill="none"/></svg>
  <div class="feature gold" style="left:508px">
    <div class="icon-box"><svg width="34" height="24" viewBox="0 0 34 24"><path d="M2 3h18v14H2zM20 8h7l5 5v4h-12z" fill="none" stroke="#b89a3a" stroke-width="2"/><circle cx="8" cy="19" r="3" fill="#b89a3a"/><circle cx="26" cy="19" r="3" fill="#b89a3a"/></svg></div>
    <h4>LOGISTICS</h4>
    <p class="small">We can deliver the car to your desired place – no need to waste time.</p>
  </div>
  <div class="feature" style="left:795px">
    <div class="icon-circle"><svg width="28" height="28" viewBox="0 0 28 28"><path d="M8 6h10a6 6 0 0 1 0 12H8M8 6l5-4M8 6l5 4M6 22h16" fill="none" stroke="#fff" stroke-width="2"/></svg></div>
    <h4>EASY CAR RENT</h4>
    <p class="small">Everything is simple – few documents and no stress.</p>
  </div>
  <div class="feature" style="left:1065px">
    <div class="icon-circle"><svg width="28" height="28" viewBox="0 0 28 28"><circle cx="14" cy="14" r="10" fill="none" stroke="#fff" stroke-width="2"/><path d="M14 8v6l4 3" stroke="#fff" stroke-width="2" fill="none"/></svg></div>
    <h4>24H SERVICE</h4>
    <p class="small">Our team is ready day and night.</p>
  </div>
</section>

<section class="sec featured">
  <h2>FEATURED CARS</h2>
  <div class="tab on" style="left:808px">NEW ARRIVALS</div>
  <div class="tab off" style="left:952px">BESTSELLING</div>
  <div class="tab off" style="left:1084px">SALE</div>
  <div class="ph" style="left:0;top:143px;width:76px;height:255px;background:linear-gradient(135deg,#5a5a5a,#222)" role="img" aria-label="Luxury car partly visible"></div>
  <div class="ph" style="left:88px;top:143px;width:313px;height:255px;background:linear-gradient(135deg,#9a9a9a,#3a3a3a)" role="img" aria-label="Grey luxury SUV parked outdoors"></div>
  <div class="ph" style="left:416px;top:143px;width:315px;height:255px;background:linear-gradient(135deg,#8a8a8a,#1e1e1e)" role="img" aria-label="Black executive van in front of a building"></div>
  <div class="ph" style="left:746px;top:143px;width:315px;height:255px;background:linear-gradient(135deg,#c5c5c5,#161616)" role="img" aria-label="Black hypercar on a road"></div>
  <div class="ph" style="left:1071px;top:143px;width:81px;height:255px;background:linear-gradient(135deg,#6b6b6b,#222)" role="img" aria-label="Luxury car partly visible"></div>
  <svg class="abs" style="left:20px;top:262px" width="28" height="16"><path d="M2 8h24M2 8l6-6M2 8l6 6" stroke="#d9bf5f" stroke-width="2" fill="none"/></svg>
  <svg class="abs" style="left:1106px;top:262px" width="28" height="16"><path d="M2 8h24M26 8l-6-6M26 8l-6 6" stroke="#d9bf5f" stroke-width="2" fill="none"/></svg>
  <div class="car-name" style="left:88px">TORVANE ULKO</div><div class="car-price" style="left:88px">2 450 PLN / day</div><div class="car-link" style="left:88px">ADD TO CART</div>
  <div class="car-name" style="left:416px">MERIDEL VANTO GS</div><div class="car-price" style="left:416px">1 990 PLN / day</div><div class="car-link" style="left:416px">ADD TO CART</div>
  <div class="car-name" style="left:746px">BRIVALDI CORSA</div><div class="car-price" style="left:746px">5 800 PLN / day</div><div class="car-link" style="left:746px">ADD TO CART</div>
</section>

<section class="sec about">
  <div class="ph" style="left:112px;top:0;width:418px;height:600px;background:linear-gradient(180deg,#2a2a2a,#8a6a52 45%,#2f3a2a 100%)" role="img" aria-label="Top view of a bride lying on the bonnet of a classic car"></div>
  <div class="offer"><div class="serif" style="font-size:40px">-50% OFF</div><div style="font-size:12px">For Every Wedding</div></div>
  <h2>ABOUT US</h2>
  <div class="txt">
    <p class="small">WestaKolory.pl was created out of a genuine love for exceptional cars. We started as two young enthusiasts with a deep appreciation for vehicles that offer more than just performance – cars that create atmosphere, emotion and presence. Over time, our private collection evolved into a premium chauffeur-driven service dedicated to weddings and refined celebrations.</p>
    <p class="small">Every car we offer is privately owned and maintained with the greatest care. We're not a typical rental company and never will be. What we deliver is personal, dedicated, and above all – uncompromising. Our chauffeurs are experienced, discreet, and always impeccably presented. Every journey is tailored, every detail considered.</p>
  </div>
  <div class="btn btn-gold" style="left:600px;top:372px;width:130px;height:36px;font-size:10px">Learn more</div>
  <div class="ph" style="left:590px;top:450px;width:165px;height:160px;background:linear-gradient(135deg,#3b5570,#0e1a26)" role="img" aria-label="Blue luxury car"></div>
  <div class="ph" style="left:765px;top:450px;width:150px;height:160px;background:linear-gradient(135deg,#50565e,#14171b)" role="img" aria-label="Dark luxury car front"></div>
  <div class="ph" style="left:925px;top:450px;width:160px;height:160px;background:linear-gradient(135deg,#7a7d82,#1b1c1e)" role="img" aria-label="Black sports car"></div>
</section>

<section class="sec faq">
  <h2>FREQUENTLY ASKED QUESTIONS</h2>
  <p class="small abs" style="left:112px;top:46px;font-size:10px">Answers to common questions about our cars, chauffeurs and how we plan your day.</p>
  <div class="faq-row" style="top:100px;height:60px">Lorem ipsum dolor sit amet, consectetur adipiscing elit?<span class="plus">+</span></div>
  <div class="faq-row" style="top:185px;height:175px">Suspendisse justo ante, condimentum id tincidunt ac, maximus imperdiet enim?<span class="plus">–</span>
    <p class="small" style="margin-top:26px;font-weight:400">Lorem ipsum dolor sit amet, consectetur adipiscing elit. Nullam eu pharetra ipsum, a tempor nunc. In malesuada viverra risus, et placerat justo sodales vel. Aliquam ipsum ante, dapibus facilisis tristique quis, elementum eget lectus. Suspendisse justo ante, condimentum id tincidunt ac, maximus imperdiet enim. Mauris commodo risus in lacus luctus, eu bibendum magna accumsan. Nunc eget dui ut dolor lacinia tincidunt sed ac nunc. Proin vel sapien mi.</p>
  </div>
  <div class="faq-row" style="top:400px;height:55px">Nam mauris felis, sagittis at maximus in, finibus sit amet dui?<span class="plus">+</span></div>
  <div class="faq-row" style="top:480px;height:55px">Nunc efficitur, ligula quis malesuada tempus, elit turpis semper est, nec euismod massa tellus quis dolor?<span class="plus">+</span></div>
</section>

<section class="sec testi">
  <h2>WHAT OUR CLIENTS SAY</h2>
  <div class="review" style="left:-200px"><span class="quote">“</span>
    <p class="small" style="position:absolute;left:30px;top:110px;width:400px">Lorem ipsum dolor sit amet, consectetur adipiscing elit, sed do eiusmod tempor incididunt ut labore et dolore magna aliqua.</p>
  </div>
  <div class="review" style="left:290px"><span class="quote">“</span>
    <div class="avatar" role="img" aria-label="Client portrait"></div>
    <div class="who"><b>TOMAS W.</b><span>Groom</span></div>
    <p class="small" style="margin-top:24px">Lorem ipsum dolor sit amet, consectetur adipiscing elit, sed do eiusmod tempor incididunt ut labore et dolore magna aliqua. Ut enim ad minim veniam, quis nostrud exercitation.</p>
    <p style="font-size:11px;margin-top:14px;font-weight:600">16 May 2025 8:00 pm</p>
  </div>
  <div class="review" style="left:780px"><span class="quote">“</span>
    <div class="avatar" role="img" aria-label="Client portrait"></div>
    <div class="who"><b>ADAM K.</b><span>Groom</span></div>
    <p class="small" style="margin-top:24px">Lorem ipsum dolor sit amet, consectetur adipiscing elit, sed do eiusmod tempor incididunt ut labore et dolore magna aliqua. Ut enim ad minim veniam, quis nostrud exercitation.</p>
    <p style="font-size:11px;margin-top:14px;font-weight:600">16 May 2025 8:00 pm</p>
  </div>
</section>

<section class="sec blogs">
  <h2>LATEST BLOGS</h2>
  <div class="ph" style="left:112px;top:75px;width:418px;height:220px;background:linear-gradient(135deg,#d8d8d8,#1a1a1a 60%,#444)" role="img" aria-label="Black stretch limousine"></div>
  <div class="abs" style="left:112px;top:312px;width:418px">
    <div class="post-title">Lorem ipsum dolor sit amet</div>
    <div class="meta">by Marek L. Dorn &nbsp;&nbsp;&nbsp;&nbsp;&nbsp;&nbsp;&nbsp;&nbsp;&nbsp;&nbsp; 16 May 2025 8:00 pm</div>
    <p class="small" style="margin-top:6px">Lorem ipsum dolor sit amet, consectetur adipiscing elit, sed do eiusmod tempor incididunt ut labore et dolore.</p>
    <div class="read">READ MORE</div>
  </div>
  <div class="abs" style="left:648px;top:0;width:1px;height:400px;background:var(--line)"></div>
  <div class="abs" style="left:670px;top:10px;width:415px">
    <div class="post-title">Lorem ipsum dolor sit amet</div>
    <div class="meta">by Marek L. Dorn</div>
    <p class="small" style="margin-top:8px">Lorem ipsum dolor sit amet, consectetur adipiscing elit, sed do eiusmod tempor incididunt ut labore et dolore magna aliqua ut enim.</p>
    <div class="read">READ MORE</div>
  </div>
  <div class="abs" style="left:670px;top:168px;width:415px;border-top:1px solid var(--line);padding-top:18px">
    <div class="post-title">Lorem ipsum dolor sit amet</div>
    <div class="meta">by Marek L. Dorn</div>
    <p class="small" style="margin-top:8px">Lorem ipsum dolor sit amet, consectetur adipiscing elit, sed do eiusmod tempor incididunt ut labore et dolore magna aliqua ut enim.</p>
    <div class="read">READ MORE</div>
  </div>
  <div class="btn btn-gold" style="left:670px;top:372px;width:170px;height:40px;font-size:10px">Explore more</div>
</section>

<section class="sec cta">
  <div class="ph" style="left:0;top:0;width:1200px;height:353px;border-radius:0;background:linear-gradient(90deg,#0d0d0f 0%,#1c2130 45%,#36476a 72%,#121620 100%)" role="img" aria-label="Groom's hand on the door of a blue luxury car"></div>
  <h2>Book Your Dream<br>Car Today</h2>
  <p class="small abs" style="left:112px;top:210px;width:420px;color:#c9c9c9">Lorem ipsum dolor sit amet, consectetur adipiscing elit, sed do eiusmod tempor incididunt ut labore et dolore magna aliqua.</p>
  <div class="btn btn-gold" style="left:112px;top:270px;width:140px;height:38px;font-size:10px">Book now</div>
</section>

<footer class="sec footer">
  <div class="abs brand" style="left:112px;top:40px;font-size:22px">WestaKolory.pl</div>
  <div class="abs" style="left:112px;top:180px;font-size:12px;color:#fff">Follow Us</div>
  <div class="social"><span></span><span></span><span></span><span></span></div>
  <div class="fcol" style="left:415px"><h5>QUICK LINKS</h5>About<br>Services<br>Blog<br>Testimonials<br>Contact</div>
  <div class="fcol" style="left:645px"><h5>MY ACCOUNT</h5>Login<br>Order History<br>Wishlist<br>Newsletter<br>Gift Certificate<br>Returns</div>
  <div class="fcol" style="left:870px"><h5>CUSTOMER SERVICE</h5>Contact Us<br>Promo Codes<br>Our Brands<br>Site Map<br>Delivery Information<br>Terms &amp; Rules</div>
  <div class="abs" style="left:112px;top:355px;width:976px;height:1px;background:#2a2a2a"></div>
  <div class="copy">Copyright © 2025. All rights reserved.</div>
</footer>

</body>
</html>
```